AI Business Tools Landing Page

My web-based website builder (Pavlora.com) will be adding many new features in the very near future and I need an eye-catching landing page to promote these new products.

The page will have a primary section of the 8 main products we are promoting:
1. AI Instant Website Generator
2. AI Chatbot
3. Online Store Builder with AI Assistance
4. AI Auto-Blogging System
5. Online Scheduling System
6. Custom Email System
7. SEO Service
8. CRM System

The page will also have a smaller section for links to our affiliate programs. These can be smaller, less-promanent buttons or links. These are the affiliate products:
1. Get Your LLC
2. Website Design and Maintenance
3. Searchly Ads Management
4. Social Media Posting Service
5. Logo Design
6. Trademark Registration
7. Patent Application
8. Printing Services (including postcards, flyers, and merch.)
9. Bulk AI Content Generator

The theme and color scheme of the page should follow the theme of our main website, which is https://pavlora.com.

I need the page fully coded and ready to deploy on my server.

I look forward to seeing your amazing designs!

```html
<!DOCTYPE html>
<html lang="en">
<head>
<meta charset="UTF-8">
<title>Pavlora – AI Business Tools</title>
<link rel="stylesheet" href="https://fonts.googleapis.com/css2?family=Lexend:wght@400;500&family=Poppins:wght@300;400&display=swap">
<style>
:root{
  --navy:#06162e;
  --navy-deep:#020814;
  --blue:#1f8ff0;
  --blue-bright:#2aa3ff;
  --ink:#0e2136;
  --body:#2a3544;
  --page:#f5f7fc;
  --white:#ffffff;
  --line:#e3e8f0;
  --icon-bg:#e8f1fb;
}
*{margin:0;padding:0;box-sizing:border-box}
html,body{width:1200px;height:2653px;overflow:hidden}
body{background:var(--white);font-family:"Poppins",sans-serif;color:var(--body);position:relative}
h1,h2,h3{font-weight:400}
.hero{position:absolute;left:0;top:0;width:1200px;height:600px;
  background:radial-gradient(circle at 900px 220px,#1a78e0 0%,#0b3f8a 28%,#061a3a 55%,var(--navy-deep) 80%)}
.hero-visual{position:absolute;left:740px;top:60px;width:330px;height:480px;border-radius:48% 48% 30% 30%;
  background:radial-gradient(circle at 50% 35%,rgba(120,200,255,.55),rgba(40,130,240,.25) 55%,rgba(20,80,180,0) 75%)}
.brand{position:absolute;left:112px;top:98px;display:flex;align-items:center;gap:18px}
.brand-dot{width:64px;height:64px;border-radius:50%;background:var(--blue-bright)}
.brand-name{font-family:"Lexend",sans-serif;font-weight:400;font-size:44px;color:var(--white)}
.hero-title{position:absolute;left:112px;top:190px;font-family:"Lexend",sans-serif;font-weight:400;font-size:40px;line-height:64px;color:var(--white);letter-spacing:.5px}
.hero-title span{color:var(--blue-bright)}
.wave{position:absolute;left:0;top:380px}
.tools{position:absolute;left:0;top:560px;width:1200px;height:1310px;background:var(--page)}
.section-title{position:absolute;left:0;width:1200px;text-align:center;font-family:"Lexend",sans-serif;font-weight:400;font-size:32px;color:var(--ink);line-height:50px}
.section-title span{color:var(--blue)}
.section-rule{position:absolute;left:572px;width:56px;height:4px;border-radius:2px;background:var(--blue)}
.card{position:absolute;width:316px;background:var(--white);box-shadow:0 2px 10px rgba(20,40,80,.06);padding:0 6px 0 20px}
.card-icon{position:absolute;left:18px;top:-30px;width:76px;height:76px;border-radius:50%;background:var(--icon-bg);border:4px solid var(--white);box-shadow:0 2px 8px rgba(20,40,80,.08);display:flex;align-items:center;justify-content:center}
.card-icon svg{width:40px;height:40px;stroke:#1c4f86;fill:none;stroke-width:1.6}
.card-rule{width:44px;height:4px;border-radius:2px;background:var(--blue)}
.card-title{font-family:"Lexend",sans-serif;font-weight:400;font-size:15px;color:var(--ink);line-height:28px;margin-top:10px;letter-spacing:.1px;white-space:nowrap}
.card-list{list-style:none;margin-top:4px}
.card-list li{position:relative;padding-left:28px;font-size:13.8px;line-height:31.7px;font-weight:300;color:var(--body)}
.card-list li::before{content:"";position:absolute;left:2px;top:10px;width:11px;height:11px;border-radius:50%;border:2px solid var(--blue)}
.card-list a{color:var(--blue);text-decoration:none}
.resources{position:absolute;left:112px;top:2105px;width:975px;height:420px;border:1px solid var(--line);display:grid;grid-template-columns:334px 351px 290px;grid-template-rows:139px 142px 139px}
.resource{border-right:1px solid var(--line);border-bottom:1px solid var(--line);display:flex;align-items:center;padding-left:26px;gap:32px}
.resource:nth-child(3n){border-right:none}
.resource:nth-child(n+7){border-bottom:none}
.resource-icon{width:64px;height:64px;flex:none;border-radius:50%;background:var(--icon-bg);display:flex;align-items:center;justify-content:center}
.resource-icon svg{width:34px;height:34px;stroke:#1c4f86;fill:none;stroke-width:1.6}
.resource-rule{width:32px;height:3px;background:var(--blue);margin-bottom:10px}
.resource-name{font-family:"Lexend",sans-serif;font-weight:400;font-size:16.5px;line-height:28px;color:var(--ink)}
.footer{position:absolute;left:0;top:2598px;width:1200px;height:55px;background:var(--navy);color:var(--white);font-family:"Lexend",sans-serif;font-size:14.5px;text-align:center;line-height:55px;letter-spacing:.3px}
</style>
</head>
<body>

<header class="hero">
  <div class="hero-visual" role="img" aria-label="Glowing digital human head with a circuit-board brain resting on an open hand"></div>
  <div class="brand"><span class="brand-dot"></span><span class="brand-name">Pavlora</span></div>
  <h1 class="hero-title">THE PREMIER AI <span>WEBSITE</span><br><span>BUILDER</span></h1>
  <svg class="wave" width="1200" height="220" viewBox="0 0 1200 220">
    <path d="M0 118 C150 60 300 30 430 40 C600 55 700 150 900 175 C1030 190 1130 160 1200 118 L1200 220 L0 220 Z" fill="#f5f7fc"/>
    <path d="M0 118 C150 60 300 30 430 40 C600 55 700 150 900 175 C1030 190 1130 160 1200 118" fill="none" stroke="#1f8ff0" stroke-width="5"/>
  </svg>
</header>

<section class="tools">
  <h2 class="section-title" style="top:0">AI BUSINESS <span>TOOLS</span></h2>
  <div class="section-rule" style="top:56px"></div>
</section>

<main>
  <article class="card" style="left:112px;top:688px;height:334px">
    <div class="card-icon"><svg viewBox="0 0 40 40"><rect x="4" y="6" width="28" height="20" rx="2"/><circle cx="26" cy="28" r="7"/><path d="M31 33l5 5"/></svg></div>
    <div class="card-rule" style="margin-top:82px"></div>
    <h3 class="card-title">AI INSTANT WEBSITE GENERATOR</h3>
    <ul class="card-list">
      <li>Get a professional, SEO-optimized website in seconds!</li>
      <li>Includes custom domain, secure high-speed hosting, professional images, and more!</li>
    </ul>
  </article>

  <article class="card" style="left:441px;top:688px;height:334px">
    <div class="card-icon"><svg viewBox="0 0 40 40"><rect x="8" y="8" width="24" height="20" rx="6"/><circle cx="16" cy="18" r="2"/><circle cx="24" cy="18" r="2"/><path d="M14 28l-2 6 6-6"/></svg></div>
    <div class="card-rule" style="margin-top:76px"></div>
    <h3 class="card-title">AI CHATBOT</h3>
    <ul class="card-list">
      <li>Fully-trainable ChatBot will learn about your business to automate the customer support process!</li>
      <li>Built-in CRM features integrate emailing, text messaging, and contact forms!</li>
    </ul>
  </article>

  <article class="card" style="left:770px;top:688px;height:334px">
    <div class="card-icon"><svg viewBox="0 0 40 40"><path d="M6 14h28l-3 14H9z"/><circle cx="13" cy="33" r="2"/><circle cx="27" cy="33" r="2"/><path d="M12 14l4-8M28 14l-4-8"/></svg></div>
    <div class="card-rule" style="margin-top:62px"></div>
    <h3 class="card-title">ONLINE STORE BUILDER<br>(E-COMMERCE) WITH AI ASSISTANCE</h3>
    <ul class="card-list">
      <li>Sell you products online and integrate your products into any website!</li>
      <li>Accept payments from multiple payment gateways including Payvex and Quillpay!</li>
    </ul>
  </article>

  <article class="card" style="left:112px;top:1078px;height:335px">
    <div class="card-icon"><svg viewBox="0 0 40 40"><rect x="10" y="10" width="20" height="20" rx="2"/><path d="M14 4v6M20 4v6M26 4v6M14 30v6M20 30v6M26 30v6M4 14h6M4 20h6M4 26h6M30 14h6M30 20h6M30 26h6"/></svg></div>
    <div class="card-rule" style="margin-top:74px"></div>
    <h3 class="card-title">AI AUTO-BLOGGING SYSTEM</h3>
    <ul class="card-list">
      <li>AI will generate an incredible blog for your business in seconds and immediately begin posting content for you!</li>
      <li>Choose from daily, weekly, or monthly automated blog posting.</li>
    </ul>
  </article>

  <article class="card" style="left:441px;top:1078px;height:335px">
    <div class="card-icon"><svg viewBox="0 0 40 40"><rect x="5" y="6" width="30" height="22" rx="2"/><path d="M15 34h10M20 28v6M10 12h20M10 17h4M18 17h4M26 17h4M10 22h4M18 22h4"/></svg></div>
    <div class="card-rule" style="margin-top:72px"></div>
    <h3 class="card-title">ONLINE SCHEDULING SYSTEM</h3>
    <ul class="card-list">
      <li>Get appointment bookings, restaurant reservations, or consultations scheduled directly from your website!</li>
      <li>Manage your employees’ schedules and all your appointments</li>
    </ul>
  </article>

  <article class="card" style="left:770px;top:1078px;height:335px">
    <div class="card-icon"><svg viewBox="0 0 40 40"><rect x="4" y="6" width="32" height="24" rx="2"/><path d="M4 12h32"/><circle cx="20" cy="22" r="6"/><path d="M14 22h12M20 16v12"/></svg></div>
    <div class="card-rule" style="margin-top:62px"></div>
    <h3 class="card-title">CUSTOM EMAILS USING YOUR<br>DOMAIN</h3>
    <ul class="card-list">
      <li>Quickly set up emails for yourself and all your employees with your own domain extension (example – <a href="#">ana@yourshop.com</a>). No more unprofessional Mailora and Yondermail email addresses!</li>
    </ul>
  </article>

  <article class="card" style="left:277px;top:1474px;height:335px">
    <div class="card-icon"><svg viewBox="0 0 40 40"><rect x="8" y="4" width="26" height="28" rx="2"/><path d="M22 26v-6M26 26v-9M30 26v-12"/><circle cx="12" cy="30" r="5"/></svg></div>
    <div class="card-rule" style="margin-top:62px"></div>
    <h3 class="card-title">CUSTOMER RELATIONSHIP<br>MANAGEMENT (CRM) SYSTEM</h3>
    <ul class="card-list">
      <li>Automate the lead follow up process to consistently stay in front of your potential customers!</li>
      <li>Schedule automatic email and text campaigns and effortlessly follow your funnels</li>
    </ul>
  </article>

  <article class="card" style="left:608px;top:1474px;height:335px">
    <div class="card-icon"><svg viewBox="0 0 40 40"><path d="M10 32a7 7 0 0 1 0-14 9 9 0 0 1 18-2 7 7 0 0 1 2 16z"/><path d="M14 14V6M20 12V4M26 14V6"/></svg></div>
    <div class="card-rule" style="margin-top:62px"></div>
    <h3 class="card-title">SEO SERVICE – AUTOMATIC<br>BACKLINK BUILDING</h3>
    <ul class="card-list">
      <li>Let us do the hard work of getting high-quality backlinks to your website. Although difficult to get, backlinks to your website boost search engine ranking more than any other strategy!</li>
    </ul>
  </article>
</main>

<section>
  <h2 class="section-title" style="top:1945px">ADDITIONAL RESOURCES TO HELP LAUNCH<br><span>YOUR BUSINESS</span></h2>
  <div class="section-rule" style="top:2058px"></div>

  <nav class="resources">
    <a class="resource"><span class="resource-icon"><svg viewBox="0 0 34 34"><path d="M6 30V8h12v22M18 14h10v16M4 30h26M10 12h4M10 17h4M10 22h4"/></svg></span><span><div class="resource-rule"></div><div class="resource-name">GET YOUR LLC</div></span></a>
    <a class="resource"><span class="resource-icon"><svg viewBox="0 0 34 34"><rect x="4" y="6" width="26" height="18" rx="2"/><path d="M13 30h8M17 24v6M8 12h10M8 17h6"/></svg></span><span><div class="resource-rule"></div><div class="resource-name">WEBSITE DESIGN AND<br>MAINTENANCE</div></span></a>
    <a class="resource"><span class="resource-icon"><svg viewBox="0 0 34 34"><path d="M6 26l9-16 9 16M11 26h14"/></svg></span><span><div class="resource-rule"></div><div class="resource-name">SEARCHLY ADS<br>MANAGEMENT</div></span></a>
    <a class="resource"><span class="resource-icon"><svg viewBox="0 0 34 34"><rect x="6" y="10" width="16" height="16" rx="2"/><rect x="16" y="4" width="12" height="12" rx="2"/><path d="M10 16h8M10 20h6"/></svg></span><span><div class="resource-rule"></div><div class="resource-name">SOCIAL MEDIA<br>POSTING SERVICE</div></span></a>
    <a class="resource"><span class="resource-icon"><svg viewBox="0 0 34 34"><rect x="4" y="4" width="26" height="26" stroke-dasharray="3 2"/><path d="M9 25l16-16M12 28l14-14"/></svg></span><span><div class="resource-rule"></div><div class="resource-name">LOGO DESIGN</div></span></a>
    <a class="resource"><span class="resource-icon"><svg viewBox="0 0 34 34"><rect x="4" y="8" width="20" height="18" rx="2"/><path d="M8 14h12M8 19h8M20 24l10-12"/></svg></span><span><div class="resource-rule"></div><div class="resource-name">TRADEMARK<br>REGISTRATION</div></span></a>
    <a class="resource"><span class="resource-icon"><svg viewBox="0 0 34 34"><rect x="7" y="4" width="18" height="26" rx="2"/><path d="M11 10h10M11 15h10M11 20h6"/><circle cx="25" cy="26" r="4"/></svg></span><span><div class="resource-rule"></div><div class="resource-name">PATENT APPLICATION</div></span></a>
    <a class="resource"><span class="resource-icon"><svg viewBox="0 0 34 34"><path d="M17 4l12 6v14l-12 6-12-6V10z"/><path d="M5 10l12 6 12-6M17 16v14"/></svg></span><span><div class="resource-rule"></div><div class="resource-name">PRINTING SERVICES</div></span></a>
    <a class="resource"><span class="resource-icon"><svg viewBox="0 0 34 34"><circle cx="17" cy="17" r="8"/><path d="M17 3v5M17 26v5M3 17h5M26 17h5M7 7l3 3M24 24l3 3M27 7l-3 3M7 27l3-3"/></svg></span><span><div class="resource-rule"></div><div class="resource-name">BULK AI CONTENT<br>GENERATOR</div></span></a>
  </nav>
</section>

<footer class="footer">© 2024 PAVLORA. ALL RIGHTS RESERVED</footer>

</body>
</html>
```